An awsome Vento salt flyer!

We need a professional looking flyer for our mineralsalt product. Named "Vento salt" coming from Maras Peru from the "Terrazales". I have an example but it's not professional looking yet. I hope you can make an amazing flyer for us! valecrestafoods.com is our webpage.
Target Market(s)
Bio shoppers, natural food lovers, healty food lovers,
Industry/Entity Type
Food Store
Requirements
Nice to have
- We would like to have a really nice professionally looking flyer. For the common flyer sizes like DL and A5. I uploaded some bag pictures too. They will be improved soon but its nice to show the product as well. The pink and yellow colors we use in the logo and package would be nice as well.

```html
<!DOCTYPE html>
<html lang="nl">
<head>
<meta charset="utf-8">
<title>Vento zout flyer</title>
<link href="https://fonts.googleapis.com/css2?family=Didact+Gothic&family=Montserrat:wght@700;800&display=swap" rel="stylesheet">
<style>
  :root{
    --pink:#e5007e;
    --crimson:#c0104f;
    --yellow:#f7c11a;
    --ink:#2a2118;
    --stage:#8d8d8d;
  }
  *{box-sizing:border-box;margin:0;padding:0}
  html,body{width:1200px;height:1200px;overflow:hidden}
  body{background:var(--stage);font-family:"Didact Gothic",sans-serif;color:var(--ink)}
  .flyer{position:absolute;left:190px;top:20px;width:820px;height:1160px;overflow:hidden;background:#efe6cf}
  .flyer-photo{position:absolute;inset:0;
    background:
      radial-gradient(ellipse 60% 18% at 55% 14%, #fbf8f1 0%, rgba(251,248,241,0) 70%),
      linear-gradient(180deg,#b7a894 0%,#ece5d6 8%,#f6f1e6 20%,#e9dcc0 32%,#dcc58c 46%,#d3b66a 60%,#cfb05d 78%,#c9aa5a 100%);}
  .accent-band{position:absolute;inset:0;width:820px;height:1160px}
  .dish{position:absolute;left:600px;top:880px;width:200px;height:200px;border-radius:50%;
    background:radial-gradient(circle,#e5d3a6 0%,#d8c08a 52%,#6d6c6a 60%,#b4b4b2 68%,#4c4c4c 74%);
    box-shadow:0 6px 16px rgba(0,0,0,.35)}
  .content{position:absolute;left:0;top:108px;width:820px;display:flex;flex-direction:column;gap:18px}
  .section-head{display:flex;align-items:center;height:44px}
  .head-block{width:54px;height:40px;background:var(--yellow);margin-top:8px;flex:none}
  .head-label{height:40px;background:var(--pink);color:#fff;font-family:"Montserrat",sans-serif;font-weight:800;
    font-size:21px;line-height:40px;padding:0 24px 0 22px;margin-left:8px;white-space:nowrap}
  .head-pixels{position:relative;width:46px;height:40px;margin-left:8px;flex:none}
  .head-pixels span{position:absolute;background:var(--pink)}
  .head-pixels span:nth-child(1){left:0;top:0;width:12px;height:12px}
  .head-pixels span:nth-child(2){left:0;top:16px;width:22px;height:22px}
  .head-pixels span:nth-child(3){left:28px;top:26px;width:11px;height:11px}
  .section-body{margin:10px 0 0 84px;font-size:16px;line-height:21px;text-align:justify}
  .section-body p+p{margin-top:16px}
  .section--wide .section-body{width:706px}
  .section--narrow .section-body{width:480px}
  .site-url{position:absolute;left:0;width:820px;top:1090px;text-align:center;font-size:23px;color:var(--ink)}
  .site-url strong{font-family:"Montserrat",sans-serif;font-weight:800}
</style>
</head>
<body>
<main class="flyer">
  <div class="flyer-photo" role="img" aria-label="Foto van witte zoutbergen bij de zoutpannen, overgaand in een close-up van gele zoutkristallen"></div>
  <svg class="accent-band" viewBox="0 0 820 1160" aria-hidden="true">
    <polygon points="820,840 820,1160 560,1160" fill="var(--crimson)"/>
    <polygon points="820,880 820,1160 600,1160" fill="#cfcac4"/>
  </svg>
  <div class="dish" role="img" aria-label="Foto van een metalen schaaltje gevuld met grove zoutkristallen"></div>

  <div class="content">
    <section class="section section--wide">
      <div class="section-head"><div class="head-block"></div><h2 class="head-label">Herkomst</h2><div class="head-pixels"><span></span><span></span><span></span></div></div>
      <div class="section-body">
        <p>Het Vento-mineraalzout komt uit Maras-Cusco in het Andesgebergte van Peru, vlakbij Machu Picchu. Hier was vroeger het Incarijk, een oud indianenvolk dat al heel ver gevorderd was om te leven met en van de natuur.</p>
        <p>Het zout is afkomstig vanuit een hele oude, schone oceaan dat in vele duizenden jaren omhoog is gestuwd in de berg. Dit bijzondere zout wordt gewonnen door de lokale bevolking op een hele prachtige locatie op zo'n 3500 meter hoogte wat het ook een heel zuiver zout maakt.</p>
      </div>
    </section>

    <section class="section section--wide">
      <div class="section-head"><div class="head-block"></div><h2 class="head-label">Natuurlijke bron</h2><div class="head-pixels"><span></span><span></span><span></span></div></div>
      <div class="section-body">
        <p>Het begint met een natuurlijk warm stroompje vanuit de berg welke via kleine riviertjes uitmondt in de zoutpontons. Als een ponton is volgestroomd wordt de toevoer geblokkeerd en vervolgens verdampt het vocht door de zon en wind en blijft het zout achter. Een heel natuurlijk en duurzaam proces wat al meer dan 2000 jaar ons voorziet van dit heerlijke zout.</p>
      </div>
    </section>

    <section class="section section--wide">
      <div class="section-head"><div class="head-block"></div><h2 class="head-label">Mineralen</h2><div class="head-pixels"><span></span><span></span><span></span></div></div>
      <div class="section-body">
        <p>Het Vento zout bevat 84 mineralen en sporenelementen waaronder: calcium, ijzer, magnesium en zink. Er zit minder natrium in het Vento zout dan de gebruikelijke zouten. Ook dit maakt het Vento zout een verstandige en betere keuze.</p>
      </div>
    </section>

    <section class="section section--wide">
      <div class="section-head"><div class="head-block"></div><h2 class="head-label">Jodium</h2><div class="head-pixels"><span></span><span></span><span></span></div></div>
      <div class="section-body">
        <p>Er is jodium aan toegevoegd wat het een compleet mineraal-keukenzout maakt. Van nature zit er onvoldoende jodium in mineraalzout om aan onze noodzakelijke behoefte te voldoen. Jodium is een essentieel mineraal voor ons lichaam. We krijgen met het nieuwe bewuste koken steeds minder jodium binnen. Maar denk ook aan het biologische brood of een dieet zonder brood. Dus kies voor een compleet zout met alle mineralen en voldoende jodium.</p>
      </div>
    </section>

    <section class="section section--narrow">
      <div class="section-head"><div class="head-block"></div><h2 class="head-label">Eerlijke handel</h2><div class="head-pixels"><span></span><span></span><span></span></div></div>
      <div class="section-body">
        <p>Wij importeren dit direct van de lokale bevolking in Peru voor een eerlijke prijs, dus het komt de lokale bevolking ook ten goede.</p>
      </div>
    </section>

    <section class="section section--narrow">
      <div class="section-head"><div class="head-block"></div><h2 class="head-label">Aanbevolen</h2><div class="head-pixels"><span></span><span></span><span></span></div></div>
      <div class="section-body">
        <p>De betere koks bevelen niets anders dan het Vento zout aan. Het is het beste en lekkerste zout van de wereld!</p>
      </div>
    </section>
  </div>

  <p class="site-url">www.<strong>valecrestafoods</strong>.com</p>
</main>
</body>
</html>
```